Water ATM Card

Need a design for water ATM cards. Size of card is 3.375 x 2.125 inch
On the Front include the Cedar hollow Logo.
Bottom right corner should have Price $100
On the Back
This card is to be used to access water refills at any Cedar Hollow Water Vending Machines.
Please contact (869) 418 2930 or (869) 534 1276 or email clearflowbox@mailvista.example for any assistance or recharging of card.

```html
<!DOCTYPE html>
<html lang="en">
<head>
<meta charset="utf-8">
<title>Cedar Hollow Water ATM Card</title>
<link rel="stylesheet" href="https://fonts.googleapis.com/css2?family=Bebas+Neue&family=Montserrat:wght@600;700;800&display=swap">
<style>
  :root {
    --page-bg: #3a3a3a;
    --card-blue: #1479c4;
    --water-light: #dcecf8;
    --water-mid: #7fb4e0;
    --ink-white: #ffffff;
    --ink-dark: #0d0d0d;
    --pill-green: #4caf3a;
    --pill-text: #1367b3;
  }
  * { margin: 0; padding: 0; box-sizing: border-box; }
  html, body { width: 1200px; height: 694px; overflow: hidden; }
  body { background: var(--page-bg); position: relative; font-family: "Montserrat", sans-serif; }

  .card {
    position: absolute; top: 177px; width: 540px; height: 340px;
    background: var(--card-blue); overflow: hidden;
  }
  .card--back { left: 40px; }
  .card--front { left: 620px; }

  .water {
    position: absolute; left: 0; right: 0; bottom: 0; height: 170px;
    background: linear-gradient(180deg, rgba(127,180,224,0) 0%, var(--water-mid) 40%, var(--water-light) 100%);
    clip-path: polygon(0 45%, 15% 38%, 30% 46%, 48% 30%, 62% 38%, 78% 18%, 100% 0, 100% 100%, 0 100%);
  }

  .back-heading {
    position: absolute; top: 22px; left: 24px; right: 24px;
    font-family: "Bebas Neue", sans-serif; color: var(--ink-white);
    font-size: 30px; line-height: 1.02; letter-spacing: 0.5px; text-align: center;
  }
  .brand-name {
    position: absolute; left: 0; right: 0; text-align: center;
    font-family: "Montserrat", sans-serif; font-weight: 800; color: var(--ink-white);
    letter-spacing: 3px; text-transform: uppercase;
  }
  .card--back .brand-name { top: 110px; font-size: 30px; }
  .back-contact {
    position: absolute; top: 180px; left: 20px; right: 20px; text-align: center;
    color: var(--ink-dark); font-weight: 700; font-size: 16px; line-height: 1.35;
  }

  .atm-pill {
    position: absolute; top: 26px; left: 34px; right: 34px; height: 44px;
    background: var(--ink-white); border-radius: 22px;
    border-bottom: 4px solid var(--pill-green);
    font-family: "Bebas Neue", sans-serif; color: var(--pill-text);
    font-size: 36px; line-height: 44px; text-align: center; letter-spacing: 0.5px;
  }
  .card--front .brand-name { top: 130px; font-size: 38px; }
  .price {
    position: absolute; right: 26px; bottom: 92px;
    color: var(--ink-dark); font-weight: 700; font-size: 24px;
  }
</style>
</head>
<body>
  <section class="card card--back">
    <div class="water" role="img" aria-label="Splashing clear water with bubbles"></div>
    <p class="back-heading">This card is to be used to access water refills<br>at any Cedar Hollow water vending machines.</p>
    <p class="brand-name">Cedar Hollow</p>
    <p class="back-contact">Contact (869) 418 2930 or (869) 534 1276<br>or email clearflowbox@mailvista.example<br>for any assistance or recharging of card.</p>
  </section>

  <section class="card card--front">
    <div class="water" role="img" aria-label="Splashing clear water with bubbles"></div>
    <p class="atm-pill">Cedar Hollow Water ATM Card</p>
    <p class="brand-name">Cedar Hollow</p>
    <p class="price">Price $100</p>
  </section>
</body>
</html>
```